New website for existing IT services company

We are a leading IT managed services provider and cloud services provider based in Sydney, Australia.
We are looking for a fresh, modern, contemporary and functional website.
We need a certain level of dynamic capabilities, such as the option to add youtube training / blog clips. So there needs to be a CMS.
Our existing website has pages including home, about us, services, contact us. Also links for remote support and connecting to our help desk system. As well as client testimonials.
The existing website is korivex.com.au however this is only posted for informational purposes. We are looking at a complete fresh re-design
We are open to the use of illustrations, however this is not a must.
I have uploaded an eps file containing our logo.
Updates
The website needs to be functional on tablets and phones as well. Added Thursday, April 30, 2015

```html
<!DOCTYPE html>
<html lang="en">
<head>
<meta charset="utf-8">
<title>Korivex Technology</title>
<link href="https://fonts.googleapis.com/css2?family=Ubuntu:wght@400;500;700&display=swap" rel="stylesheet">
<style>
:root{
  --blue:#1f8fd2;
  --nav-active:#3fb0e0;
  --hero-top:#3db4e4;
  --hero-bottom:#0e4fae;
  --ink:#1b1b1b;
  --text:#333;
  --muted:#555;
  --panel:#f0f0f0;
  --rule:#d4d4d4;
  --footer:#efefef;
}
*{margin:0;padding:0;box-sizing:border-box}
html,body{width:853px;height:1200px;overflow:hidden;background:#fff}
body{font-family:"Ubuntu",sans-serif;color:var(--text);position:relative}
.abs{position:absolute}

.header{left:0;top:0;width:853px;height:61px;background:#fff}
.brand{left:106px;top:14px;font-size:26px;font-weight:700;color:var(--ink);letter-spacing:-.5px;display:flex;align-items:center;gap:6px}
.brand .mark{width:12px;height:12px;background:var(--blue)}
.nav{left:497px;top:23px;display:flex;height:38px;font-size:10px;color:var(--ink)}
.nav a{display:flex;align-items:center;padding:0 9px;color:inherit;text-decoration:none;height:38px}
.nav a.active{background:var(--nav-active);color:#fff;width:61px;justify-content:center;margin-right:2px}

.hero{left:0;top:61px;width:853px;height:327px;background:linear-gradient(var(--hero-top),var(--hero-bottom))}
.hero h1{left:78px;top:122px;font-size:23px;font-weight:500;color:#fff}
.hero p{left:79px;top:159px;width:280px;font-size:11px;line-height:18px;color:#0d1f3a}
.btn{left:79px;top:205px;width:102px;height:29px;background:#000;color:#fff;font-size:10px;font-weight:500;display:flex;align-items:center;justify-content:center}
.hero-visual{left:395px;top:64px;width:340px;height:205px;background:linear-gradient(#1a2a44,#0b1220 70%,rgba(14,79,174,0));}
.dots{left:391px;top:302px;display:flex;gap:6px}
.dots i{width:5px;height:5px;border-radius:50%;background:#fff}
.dots i:first-child{background:#0a1a3a}

.partners{left:0;top:388px;width:853px;height:67px;background:#fff;box-shadow:0 6px 10px rgba(0,0,0,.06);display:flex;align-items:center;justify-content:center;gap:58px;font-size:13px;font-weight:700;color:#2a2a2a}

.services{left:79px;top:506px;display:flex;gap:25px}
.tile{width:119px;height:103px;background:#000;color:#fff;font-size:9px;font-weight:500;text-align:center;position:relative}
.tile svg{position:absolute;left:34px;top:14px}
.tile span{position:absolute;left:0;right:0;top:79px}

.panel{top:654px;width:219px;height:155px;background:var(--panel);padding:14px 12px}
.panel h2{font-size:14px;font-weight:500;color:var(--blue);margin-bottom:12px}
.news{left:79px}
.news .date{font-size:9px;font-weight:700;color:#111;margin-left:2px}
.news h3{font-size:10px;font-weight:400;color:#111;margin:2px 0 6px 2px}
.news p{font-size:7.5px;line-height:13.4px;color:var(--muted)}
.clients{left:317px}
.clients .quote{font-size:18px;font-weight:700;color:var(--blue);line-height:10px;height:12px}
.clients p{font-size:7.5px;line-height:14.6px;color:var(--muted);margin:2px 0 6px 16px}
.clients .who{font-size:10px;font-weight:500;color:var(--blue);margin-left:16px}

.cta{left:557px;width:217px;height:73px;background:var(--blue);color:#fff}
.cta svg{position:absolute;left:8px;top:22px}
.cta h2{position:absolute;left:54px;top:21px;font-size:14px;font-weight:500}
.cta p{position:absolute;left:56px;top:42px;font-size:9.5px;word-spacing:1px}
.remote{top:655px}
.help{top:736px}

.sec-title{top:855px;font-size:14px;font-weight:500;color:var(--blue)}
.rule{top:884px;height:1px;background:var(--rule)}
.arrows{left:753px;top:860px;font-size:13px;color:#111;letter-spacing:4px}
.video{left:79px;top:901px;width:339px;height:195px;background:linear-gradient(90deg,#e6e8ea 0%,#c9ccd0 45%,#3a3d42 80%,#6c7075 100%)}
.blog-img{left:437px;width:159px;height:87px}
.b1{top:902px;background:linear-gradient(90deg,#2b3038,#1a1d22 60%,#dfe2e6)}
.b2{top:1011px;background:linear-gradient(90deg,#1c2a38,#33424e 55%,#d8dbdf)}
.post{left:612px;width:165px}
.post b{display:block;font-size:9px;color:#111;margin-bottom:8px}
.post p{font-size:9px;line-height:15px;color:var(--muted)}

.footer{left:0;top:1127px;width:853px;height:73px;background:var(--footer);font-size:9.5px;color:#222}
.footer .links{position:absolute;left:79px;top:22px;word-spacing:2px}
.footer .links em{font-style:normal;margin:0 10px}
.footer .copy{position:absolute;left:79px;top:45px}
.footer .legal{position:absolute;right:79px;top:31px}
</style>
</head>
<body>

<header class="abs header">
  <div class="abs brand">KORIVEX<span class="mark"></span></div>
  <nav class="abs nav">
    <a class="active">Home</a><a>About Us</a><a>Services</a><a>Store</a><a>Contact Us</a>
  </nav>
</header>

<section class="abs hero">
  <h1 class="abs">Korivex Technology</h1>
  <p class="abs">Access your desktop, applications and data from any PC, anywhere in the world.</p>
  <div class="abs btn">Learn More</div>
  <div class="abs hero-visual" role="img" aria-label="Row of server rack cabinets"></div>
  <div class="abs dots"><i></i><i></i><i></i><i></i></div>
</section>

<section class="abs partners">
  <span>Lumora</span><span>Cirvanta</span><span>Jessamine</span><span>Tandrel</span><span>Solvane</span><span>Hexlo</span>
</section>

<section class="abs services">
  <div class="tile">
    <svg width="52" height="50" viewBox="0 0 52 50"><path d="M4 22 L16 12 L26 18 L36 12 L48 22 L38 36 L30 40 L16 34 Z" fill="var(--blue)"/></svg>
    <span>Out Sourced IT Services</span></div>
  <div class="tile">
    <svg width="52" height="52" viewBox="0 0 52 52"><rect x="2" y="6" width="14" height="40" fill="var(--blue)"/><rect x="18" y="4" width="32" height="26" fill="none" stroke="var(--blue)" stroke-width="4"/><rect x="28" y="32" width="12" height="6" fill="var(--blue)"/><rect x="20" y="40" width="28" height="4" fill="var(--blue)"/></svg>
    <span>Hosted Solutions</span></div>
  <div class="tile">
    <svg width="52" height="52" viewBox="0 0 52 52"><circle cx="26" cy="26" r="22" fill="none" stroke="var(--blue)" stroke-width="4"/><path d="M14 14 Q24 10 28 18 Q24 26 18 30 Q12 24 14 14Z M30 28 Q40 26 40 36 Q34 42 30 40Z" fill="var(--blue)"/></svg>
    <span>Managed Exchange</span></div>
  <div class="tile">
    <svg width="52" height="56" viewBox="0 0 52 56"><rect x="20" y="4" width="8" height="26" rx="4" fill="var(--blue)"/><path d="M14 26 Q14 22 20 24 L36 24 Q42 26 40 36 L38 52 L18 52 Q12 40 14 26Z" fill="var(--blue)"/></svg>
    <span>Internet Services</span></div>
  <div class="tile">
    <svg width="52" height="50" viewBox="0 0 52 50"><path d="M2 6 L10 6 L16 30 L44 30 L48 12 L12 12" fill="none" stroke="var(--blue)" stroke-width="4"/><rect x="16" y="14" width="28" height="12" fill="var(--blue)"/><circle cx="20" cy="40" r="4" fill="var(--blue)"/><circle cx="40" cy="40" r="4" fill="var(--blue)"/></svg>
    <span>Shop Online</span></div>
</section>

<article class="abs panel news">
  <h2>News</h2>
  <div class="date">April 30 th ,2015</div>
  <h3>Email - Under the Covers</h3>
  <p>Lorem Ipsum is simply dummy text of the printing and typesetting industry. Lorem Ipsum has been the industry's standard dummy text ever since the 1500s, when an unknown printer took a galley of type and scrambled it to make a type specimen book.</p>
</article>

<article class="abs panel clients">
  <h2>Clients</h2>
  <div class="quote">&ldquo;</div>
  <p>Korivex is just wonderful. The guys are always willing to help if my computer is playing up and patiently sort out all my glitches. They are immensely professional yet always friendly and supportive.</p>
  <div class="who">Marla Quinton</div>
</article>

<a class="abs cta remote">
  <svg width="38" height="36" viewBox="0 0 38 36"><path d="M4 34 L4 18 Q4 4 19 4 Q34 4 34 18 L34 34Z" fill="none" stroke="#111" stroke-width="3.5"/><line x1="4" y1="24" x2="34" y2="24" stroke="#111" stroke-width="3"/><circle cx="19" cy="16" r="4" fill="none" stroke="#111" stroke-width="3"/></svg>
  <h2>Remote Support</h2>
  <p>Download Our Tailored Software</p>
</a>
<a class="abs cta help">
  <svg width="38" height="34" viewBox="0 0 38 34"><ellipse cx="15" cy="13" rx="12" ry="10" fill="none" stroke="#111" stroke-width="3.5"/><ellipse cx="25" cy="21" rx="9" ry="8" fill="#111"/><path d="M30 27 L34 33 L26 29Z" fill="#111"/></svg>
  <h2>Help Desk</h2>
  <p>Open A Support Request</p>
</a>

<h2 class="abs sec-title" style="left:78px">Featured Video</h2>
<div class="abs rule" style="left:79px;width:339px"></div>
<div class="abs video" role="img" aria-label="Technician working on a laptop beside server racks"></div>

<h2 class="abs sec-title" style="left:435px">Blog</h2>
<div class="abs arrows">&lsaquo;&rsaquo;</div>
<div class="abs rule" style="left:436px;width:339px"></div>
<div class="abs blog-img b1" role="img" aria-label="Server room aisle"></div>
<div class="abs post" style="top:913px"><b>April 30 th ,2015</b><p>Neque porro quisquam est qui dolorem ipsum quia dolor sit amet, consectetur, adipisci velit...</p></div>
<div class="abs blog-img b2" role="img" aria-label="Two engineers checking a server rack"></div>
<div class="abs post" style="top:1022px"><b>April 30 th ,2015</b><p>Neque porro quisquam est qui dolorem ipsum quia dolor sit amet, consectetur, adipisci velit...</p></div>

<footer class="abs footer">
  <div class="links">Home<em>|</em>About Us<em>|</em>Services<em>|</em>Store<em>|</em>Contact Us</div>
  <div class="copy">&copy; 2015 Company Name, All Rights Reserved</div>
  <div class="legal">Contact Us | Terms of Use | Privacy Policy | Sitemap</div>
</footer>

</body>
</html>
```